Construction material supplies company business card ****

1. Full company name “K T Masonry Works Ltd”
I am after a Business card design for the company as a whole. We are better known in Solomon Islands as “K T Masonry” for short.

We are a building materials supplier of
Ready Mixed Concrete, Bricks and Blocks,
Quarry products- gravel, aggregates, sand etc.
Cement distributor/retailer of reputable brands.
Other prefab concrete products. Culverts, wave breakers, concrete retaining blocks etc.

2. Competitive Advantage over Competition: Quality, efficient, professional, dependable, reliable

3. We want people to feel trust worthy, high quality, strong when they see our brand

5. No preference to color. Maybe more sturdy and corporate. Not fancy.

Industry/Entity Type

CONSTRUCTION SUPPLY

Contact Information for Business Card

Name, Position, office phone mob phone, email

Requirements
Must have
• the company logo
Nice to have
• would like to see a mixture of designs, of with logo only and also with simple graphic designs to bring out the company whilst still have the strong sturdy professional feeling

```html
<!DOCTYPE html>
<html lang="en">
<head>
<meta charset="utf-8">
<title>K T Masonry Works Ltd – Business Card</title>
<link href="https://fonts.googleapis.com/css2?family=Orbitron:wght@600;700&family=Open+Sans:wght@400&display=swap" rel="stylesheet">
<style>
  :root {
    --backdrop: #2a2a2a;
    --card-deep: #0e4166;
    --card-light: #245677;
    --ink: #ffffff;
    --ink-soft: rgba(255, 255, 255, 0.92);
  }
  * { margin: 0; padding: 0; box-sizing: border-box; }
  html, body {
    width: 1200px;
    height: 900px;
    overflow: hidden;
    background: var(--backdrop);
  }
  .stage {
    position: relative;
    width: 1200px;
    height: 900px;
  }
  .card {
    position: absolute;
    left: 250px;
    width: 700px;
    height: 400px;
    background: linear-gradient(110deg, var(--card-deep) 0%, var(--card-deep) 45%, var(--card-light) 100%);
    color: var(--ink);
  }
  .card--front { top: 40px; }
  .card--back { top: 465px; }

  /* Front: wordmark */
  .wordmark {
    position: absolute;
    right: 62px;
    bottom: 62px;
    display: flex;
    align-items: center;
    gap: 14px;
    font-family: "Orbitron", sans-serif;
    font-weight: 700;
    color: var(--ink);
  }
  .wordmark__square {
    width: 30px;
    height: 30px;
    background: var(--ink);
  }
  .wordmark__text {
    display: flex;
    flex-direction: column;
    line-height: 1.05;
  }
  .wordmark__main { font-size: 24px; letter-spacing: 1px; }
  .wordmark__sub { font-size: 12.5px; letter-spacing: 3.2px; }

  /* Back: person and contacts */
  .details {
    position: absolute;
    top: 170px;
    left: 0;
    right: 0;
    display: flex;
    align-items: center;
  }
  .person {
    width: 360px;
    text-align: right;
    padding-right: 22px;
  }
  .person__name {
    font-family: "Orbitron", sans-serif;
    font-weight: 700;
    font-size: 27px;
    letter-spacing: 1px;
    line-height: 1.1;
  }
  .person__role {
    font-family: "Open Sans", sans-serif;
    font-size: 16px;
    color: var(--ink-soft);
    margin-top: 4px;
  }
  .divider {
    width: 2px;
    height: 56px;
    background: var(--ink);
  }
  .contacts {
    list-style: none;
    padding-left: 26px;
    font-family: "Open Sans", sans-serif;
    font-size: 15.5px;
    line-height: 1.5;
  }
  .contacts__item {
    display: flex;
    align-items: center;
    gap: 12px;
  }
  .contacts__icon {
    width: 14px;
    height: 14px;
    flex: none;
  }
</style>
</head>
<body>
  <main class="stage">
    <section class="card card--front" aria-label="Business card front">
      <div class="wordmark">
        <span class="wordmark__square" aria-hidden="true"></span>
        <span class="wordmark__text">
          <span class="wordmark__main">K T MASONRY</span>
          <span class="wordmark__sub">WORKS LTD</span>
        </span>
      </div>
    </section>

    <section class="card card--back" aria-label="Business card back">
      <div class="details">
        <div class="person">
          <p class="person__name">DANIEL HARPER</p>
          <p class="person__role">Founder and CEO</p>
        </div>
        <span class="divider" aria-hidden="true"></span>
        <ul class="contacts">
          <li class="contacts__item">
            <svg class="contacts__icon" viewBox="0 0 24 24" aria-hidden="true"><path fill="#fff" d="M6.6 10.8a15.1 15.1 0 0 0 6.6 6.6l2.2-2.2a1 1 0 0 1 1-.25 11.4 11.4 0 0 0 3.6.57 1 1 0 0 1 1 1V20a1 1 0 0 1-1 1A17 17 0 0 1 3 4a1 1 0 0 1 1-1h3.5a1 1 0 0 1 1 1c0 1.25.2 2.45.57 3.57a1 1 0 0 1-.25 1z"/></svg>
            <span>000 000 0000</span>
          </li>
          <li class="contacts__item">
            <svg class="contacts__icon" viewBox="0 0 24 24" aria-hidden="true"><rect x="6" y="2" width="12" height="20" rx="2" fill="none" stroke="#fff" stroke-width="2"/><line x1="11" y1="18" x2="13" y2="18" stroke="#fff" stroke-width="2"/></svg>
            <span>000 000 0000</span>
          </li>
          <li class="contacts__item">
            <svg class="contacts__icon" viewBox="0 0 24 24" aria-hidden="true"><rect x="2" y="5" width="20" height="14" rx="1" fill="none" stroke="#fff" stroke-width="2"/><path d="M2 6l10 7 10-7" fill="none" stroke="#fff" stroke-width="2"/></svg>
            <span>info@ktmasonry.com.au</span>
          </li>
        </ul>
      </div>
    </section>
  </main>
</body>
</html>
```